Corporate Business Card

Very professional, Modern, Not to busy, include phone address email, website
(253) 617-4930, 18761 52nd Avenue S, Kent, WA 98047, martin@plumlinegroup.com, varkoworks.com

Target Market(s)

Manufacturing

Industry/Entity Type

Aero, machining, manufacturing, Off road racing

Contact Information for Business Card

Phone, address email, website

```html
<!DOCTYPE html>
<html lang="en">
<head>
<meta charset="utf-8">
<title>Varko Works – Business Card</title>
<link href="https://fonts.googleapis.com/css2?family=Open+Sans:wght@400;600;700&display=swap" rel="stylesheet">
<style>
  :root {
    --page-bg: #8b8b89;
    --navy: #17356b;
    --navy-back: #213670;
    --navy-soft: #3a5194;
    --navy-deep: #172a5c;
    --red: #d7232e;
    --white: #ffffff;
  }
  * { margin: 0; padding: 0; box-sizing: border-box; }
  html, body { width: 1200px; height: 801px; overflow: hidden; }
  body {
    background: var(--page-bg);
    font-family: "Open Sans", Arial, sans-serif;
    position: relative;
  }
  .card {
    position: absolute;
    top: 258px;
    width: 500px;
    height: 286px;
    border-radius: 18px;
    overflow: hidden;
    box-shadow: 0 10px 24px rgba(0,0,0,0.28);
    border: 1px solid var(--red);
  }
  .card--front { left: 60px; background: var(--white); }
  .card--back { left: 640px; background: var(--navy-back); }
  .card__art { position: absolute; inset: 0; width: 100%; height: 100%; }

  .brand {
    position: absolute;
    left: 28px;
    top: 150px;
  }
  .brand__name {
    font-weight: 700;
    font-size: 24px;
    color: var(--navy);
    letter-spacing: 0.3px;
    line-height: 1;
    white-space: nowrap;
  }
  .brand__rule {
    margin-top: 12px;
    width: 120px;
    height: 2px;
    background: var(--navy);
  }

  .contact {
    position: absolute;
    right: 26px;
    top: 62px;
    text-align: right;
    color: var(--white);
    font-size: 13px;
    line-height: 1.45;
  }
  .contact__company { color: var(--red); font-weight: 600; font-size: 14px; }
  .contact__line { display: flex; justify-content: flex-end; align-items: center; gap: 7px; }
  .contact__icon { width: 11px; height: 11px; flex: none; }

  .back-brand {
    position: absolute;
    left: 0; right: 0;
    top: 108px;
    text-align: center;
  }
  .back-brand__name {
    font-weight: 700;
    font-size: 52px;
    color: var(--navy-soft);
    letter-spacing: 1px;
    line-height: 1;
  }
  .back-brand__rule {
    margin: 18px auto 0;
    width: 240px;
    height: 2px;
    background: var(--navy-deep);
  }
</style>
</head>
<body>
  <section class="card card--front" aria-label="Business card front">
    <svg class="card__art" viewBox="0 0 500 286" preserveAspectRatio="none" aria-hidden="true">
      <path d="M300,0 C220,40 210,230 92,286" fill="none" stroke="var(--red)" stroke-width="6"/>
      <path d="M318,0 C236,44 226,236 108,286" fill="none" stroke="var(--navy)" stroke-width="2.5"/>
      <path d="M332,0 L500,0 L500,286 L122,286 C240,238 250,48 332,0 Z" fill="var(--navy)"/>
    </svg>

    <div class="brand">
      <div class="brand__name">Varko Works</div>
      <div class="brand__rule"></div>
    </div>

    <div class="contact">
      <div class="contact__company">Varko Works</div>
      <div>18761 52nd Avenue S</div>
      <div>Kent, WA 98047</div>
      <div class="contact__line">(253) 617-4930
        <svg class="contact__icon" viewBox="0 0 12 12" aria-hidden="true"><path d="M2.5 1 L4.5 1 L5.3 3.5 L4 4.5 C4.6 5.9 6.1 7.4 7.5 8 L8.5 6.7 L11 7.5 L11 9.5 C11 10.3 10.3 11 9.5 11 C5 11 1 7 1 2.5 C1 1.7 1.7 1 2.5 1 Z" fill="var(--red)"/></svg>
      </div>
      <div class="contact__line">martin@plumlinegroup.com
        <svg class="contact__icon" viewBox="0 0 12 12" aria-hidden="true"><rect x="1" y="2.5" width="10" height="7" rx="1" fill="var(--red)"/><path d="M1.5 3 L6 6.5 L10.5 3" fill="none" stroke="var(--navy)" stroke-width="1"/></svg>
      </div>
      <div class="contact__line">varkoworks.com
        <svg class="contact__icon" viewBox="0 0 12 12" aria-hidden="true"><circle cx="6" cy="6" r="5" fill="var(--red)"/><path d="M1 6 H11 M6 1 C3.5 3.5 3.5 8.5 6 11 M6 1 C8.5 3.5 8.5 8.5 6 11" fill="none" stroke="var(--navy)" stroke-width="0.8"/></svg>
      </div>
    </div>
  </section>

  <section class="card card--back" aria-label="Business card back">
    <div class="back-brand">
      <div class="back-brand__name">Varko Works</div>
      <div class="back-brand__rule"></div>
    </div>
  </section>
</body>
</html>
```